Corporate Design für Malermeister
Zielgruppe
Ich bin Malermeister ,
wir bieten komplettrenovierungen an vom Gestalten der Oberflächen, kreative Wandgestaltung Trockenbau, Bodenverlegearbeiten Parkett, Laminat, Teppich, designböden etc.
Fokus liegt bei den Malerarbeiten! Auch Fassaden werden restaurariert und gestaltet
Wir wollen modern und hochwertig rüber kommen
Aufgabenstellung
Das Logo soll zeigen, dass wir ein moderner kreativer Betrieb sind
da wir eine Diesntaleistung anbieten sollte es auch auf Vertrauen asutrahlen

```html
<!DOCTYPE html>
<html lang="de">
<head>
<meta charset="utf-8">
<title>Visitenkarte Raumkontor – Entwurf 03</title>
<link rel="stylesheet" href="https://fonts.googleapis.com/css2?family=PT+Sans:wght@400;700&family=Roboto+Condensed:wght@300;700&display=swap">
<style>
  :root {
    --frame-blue: #0e6fb7;
    --brand-blue: #0e6fb7;
    --text-grey: #555555;
    --caption-grey: #9a9a9a;
    --card-bg: #f4f4f4;
    --page-bg: #ffffff;
  }
  * { box-sizing: border-box; margin: 0; padding: 0; }
  html, body { width: 1200px; height: 1200px; overflow: hidden; }
  body {
    background: var(--page-bg);
    border: 15px solid var(--frame-blue);
    position: relative;
    font-family: "PT Sans", sans-serif;
    color: var(--text-grey);
  }
  .presentation-caption {
    position: absolute; top: 168px; left: 0; width: 1170px;
    text-align: center; color: var(--caption-grey);
    font-size: 20px; line-height: 28px;
  }
  .card {
    position: absolute; top: 362px; width: 420px; height: 648px;
    background: var(--card-bg);
    box-shadow: 0 2px 10px rgba(0,0,0,0.28);
  }
  .card--front { left: 103px; }
  .card--back { left: 646px; }
  .brand {
    position: absolute; left: 148px; top: 186px;
  }
  .brand__name {
    font-family: "Roboto Condensed", sans-serif; font-weight: 700;
    font-size: 50px; line-height: 54px; color: var(--brand-blue);
    letter-spacing: -0.5px;
  }
  .brand__trade {
    font-family: "Roboto Condensed", sans-serif; font-weight: 700;
    font-size: 22px; line-height: 26px; letter-spacing: 0.6px;
    color: var(--text-grey); margin-top: 2px;
  }
  .brand__tagline {
    font-family: "Roboto Condensed", sans-serif; font-weight: 300;
    font-size: 18px; line-height: 24px; color: var(--text-grey);
  }
  .contact { position: absolute; left: 148px; top: 328px; font-size: 19px; line-height: 26px; }
  .contact__name { color: var(--brand-blue); font-weight: 700; font-size: 21px; line-height: 24px; }
  .contact__role { margin-bottom: 22px; }
  .contact__row { position: relative; }
  .contact__row svg {
    position: absolute; left: -32px; top: 3px; width: 21px; height: 21px; fill: var(--brand-blue);
  }
  .contact__address { margin-bottom: 28px; }
  .contact__phone { margin-bottom: 26px; }
  .contact__web { color: var(--brand-blue); font-weight: 700; }
  .services { position: absolute; left: 148px; top: 328px; font-size: 19px; line-height: 21.5px; }
  .services__heading { color: var(--brand-blue); font-weight: 700; font-size: 21px; line-height: 24px; }
  .services__list { list-style: none; margin-bottom: 20px; }
  .services__list li { position: relative; }
  .services__list li::before {
    content: ""; position: absolute; left: -23px; top: 10px;
    width: 3px; height: 3px; border-radius: 50%; background: var(--brand-blue);
  }
</style>
</head>
<body>
  <div class="presentation-caption">
    Visitenkarte Raumkontor - Entwurf 03 &nbsp;|&nbsp; Seite 1 + 2<br>
    Standard 85 x 55 mm &nbsp;|&nbsp; hochkant<br>
    zweiseitig 4 c
  </div>

  <section class="card card--front">
    <div class="brand">
      <div class="brand__name">Raumkontor</div>
      <div class="brand__trade">MALERMEISTERBETRIEB</div>
      <div class="brand__tagline">Altes erhalten | Neues gestalten</div>
    </div>
    <div class="contact">
      <div class="contact__name">Jonas Velten</div>
      <div class="contact__role">Malermeister</div>
      <div class="contact__row contact__address">
        <svg viewBox="0 0 24 24" aria-hidden="true"><path d="M12 3 1 12h3v9h6v-6h4v6h6v-9h3z"/></svg>
        Lindenweg 14<br>59821 Talheim
      </div>
      <div class="contact__row contact__phone">
        <svg viewBox="0 0 24 24" aria-hidden="true"><path d="M7 1h10a2 2 0 0 1 2 2v18a2 2 0 0 1-2 2H7a2 2 0 0 1-2-2V3a2 2 0 0 1 2-2zm0 3v14h10V4zm5 15.2a1 1 0 1 0 0 2 1 1 0 0 0 0-2z"/></svg>
        0151 - 482 17 39
      </div>
      <div class="contact__row contact__mail">
        <svg viewBox="0 0 24 24" aria-hidden="true"><path d="M2 5h20v2l-10 6L2 7zm0 4.3 10 6 10-6V19H2z"/></svg>
        maler@raumkontor.de
      </div>
      <div class="contact__row contact__web">
        <svg viewBox="0 0 24 24" aria-hidden="true"><path d="M12 2a10 10 0 1 0 0 20 10 10 0 0 0 0-20zm-1 17.9A8 8 0 0 1 4.2 10L9 15v1a2 2 0 0 0 2 2zm6.9-2.5A2 2 0 0 0 16 16h-1v-3a1 1 0 0 0-1-1H8v-2h2a1 1 0 0 0 1-1V7h2a2 2 0 0 0 2-2v-.4a8 8 0 0 1 2.9 12.8z"/></svg>
        www.raumkontor.de
      </div>
    </div>
  </section>

  <section class="card card--back">
    <div class="brand">
      <div class="brand__name">Raumkontor</div>
      <div class="brand__trade">MALERMEISTERBETRIEB</div>
      <div class="brand__tagline">Altes erhalten | Neues gestalten</div>
    </div>
    <div class="services">
      <div class="services__heading">Malerarbeiten</div>
      <ul class="services__list">
        <li>Malen &amp; Tapezieren</li>
        <li>Gestalten von Oberflächen</li>
        <li>kreative Wandgestaltung</li>
        <li>Fassadengestalung</li>
        <li>Restaurierung</li>
      </ul>
      <div class="services__heading">Innenarbeiten</div>
      <ul class="services__list">
        <li>Teppich</li>
        <li>Laminat</li>
        <li>Parkett</li>
        <li>Designerböden</li>
        <li>Trockenbau</li>
      </ul>
    </div>
  </section>
</body>
</html>
```